Brellwick Partners, LLC Stationary

Brellwick Partners, LLC is a new financial planning and consulting company. We are looking for designs on business cards, letterhead, envelopes, and anything else that would be useful. Our preference for business card design is two sided. We are looking for a professional and clean look with incorporating the logo and patriotic feel. Thank you to all who participate and good luck!

```html
<!DOCTYPE html>
<html lang="en">
<head>
<meta charset="utf-8">
<title>Brellwick Partners, LLC — Business Card</title>
<link href="https://fonts.googleapis.com/css2?family=Exo+2:wght@400;500;600&display=swap" rel="stylesheet">
<style>
  :root {
    --stage: #3b3b3b;
    --paper: #f6f6f6;
    --red: #be1e24;
    --navy: #0f3a66;
    --ink: #444444;
  }
  html, body {
    margin: 0;
    width: 1200px;
    height: 750px;
    overflow: hidden;
    background: var(--stage);
    font-family: "Exo 2", sans-serif;
  }
  .stage {
    position: relative;
    width: 1200px;
    height: 750px;
  }
  .card {
    position: absolute;
    width: 461px;
    height: 263px;
    background: var(--paper);
    overflow: hidden;
  }
  .card-front { left: 428px; top: 124px; }
  .card-back  { left: 284px; top: 403px; }

  .card-art {
    position: absolute;
    inset: 0;
    width: 100%;
    height: 100%;
  }

  .wordmark {
    position: absolute;
    left: 20px;
    top: 24px;
    display: flex;
    align-items: center;
    gap: 8px;
  }
  .wordmark-dot {
    width: 18px;
    height: 18px;
    border-radius: 50%;
    background: var(--navy);
  }
  .wordmark-name {
    font-size: 20px;
    font-weight: 600;
    color: var(--navy);
    letter-spacing: 0.02em;
  }
  .tagline {
    position: absolute;
    left: 46px;
    top: 52px;
    font-size: 6.5px;
    letter-spacing: 0.14em;
    color: var(--red);
    text-transform: uppercase;
  }

  .details {
    position: absolute;
    right: 24px;
    top: 82px;
    text-align: right;
    color: var(--ink);
  }
  .person-name {
    margin: 0;
    font-size: 18px;
    line-height: 20px;
    font-weight: 600;
    color: var(--red);
    letter-spacing: 0.04em;
    text-transform: uppercase;
  }
  .person-title {
    margin: 1px 0 0;
    font-size: 14px;
    line-height: 18px;
    font-weight: 400;
    color: var(--navy);
    letter-spacing: 0.04em;
    text-transform: uppercase;
  }
  .address {
    margin: 12px 0 0;
    font-style: normal;
    font-size: 13px;
    line-height: 17px;
  }
  .contact-list {
    list-style: none;
    margin: 10px 0 0;
    padding: 0;
    font-size: 13px;
    line-height: 18.5px;
  }
  .contact-list li {
    display: flex;
    justify-content: flex-end;
    align-items: center;
    gap: 7px;
  }
  .contact-list li:nth-child(n+3) { font-size: 12px; }
  .icon {
    width: 12px;
    height: 12px;
    fill: var(--red);
    flex: none;
  }
</style>
</head>
<body>
<main class="stage">

  <section class="card card-front" aria-label="Business card front">
    <svg class="card-art" viewBox="0 0 461 263" role="img" aria-label="Large red eagle head illustration with navy chest">
      <defs>
        <linearGradient id="front-art-fill" x1="0" y1="0" x2="1" y2="0.4">
          <stop offset="0" stop-color="#be1e24"/>
          <stop offset="0.65" stop-color="#be1e24"/>
          <stop offset="1" stop-color="#0f3a66"/>
        </linearGradient>
      </defs>
      <polygon points="0,253 170,110 340,88 461,180 461,263 0,263" fill="url(#front-art-fill)"/>
    </svg>
    <div class="wordmark">
      <span class="wordmark-dot"></span>
      <span class="wordmark-name">Brellwick Partners, LLC</span>
    </div>
    <div class="tagline">Financial planning and consulting</div>
  </section>

  <section class="card card-back" aria-label="Business card back">
    <svg class="card-art" viewBox="0 0 461 263" role="img" aria-label="Red and navy eagle wing feather illustration">
      <defs>
        <linearGradient id="back-art-fill" x1="0" y1="0" x2="1" y2="0">
          <stop offset="0" stop-color="#0f3a66"/>
          <stop offset="0.45" stop-color="#be1e24"/>
          <stop offset="1" stop-color="#be1e24"/>
        </linearGradient>
      </defs>
      <polygon points="0,0 402,0 52,263 0,263" fill="url(#back-art-fill)"/>
    </svg>

    <div class="details">
      <h1 class="person-name">Owen Pryce</h1>
      <p class="person-title">CEO/Founder</p>
      <address class="address">2140 Larkspur Court<br>Juneau, Alaska 34612</address>
      <ul class="contact-list">
        <li>555 214 7790
          <svg class="icon" viewBox="0 0 12 12" aria-hidden="true"><path d="M2.5 0.5l2 2.2-1 1.4c.7 1.6 1.8 2.7 3.4 3.4l1.4-1 2.2 2-1.3 1.9C4.6 10 2 7.4 0.6 1.8z"/></svg>
        </li>
        <li>555 214 7791
          <svg class="icon" viewBox="0 0 12 12" aria-hidden="true"><rect x="3" y="0.5" width="6" height="3"/><rect x="0.5" y="4" width="11" height="5" rx="1"/><rect x="3" y="8" width="6" height="3.5" fill="#f6f6f6" stroke="#be1e24" stroke-width="1"/></svg>
        </li>
        <li>hello@brellwick.com
          <svg class="icon" viewBox="0 0 12 12" aria-hidden="true"><rect x="0.5" y="2" width="11" height="8"/><path d="M1 2.5l5 4 5-4" fill="none" stroke="#f6f6f6" stroke-width="1"/></svg>
        </li>
        <li>www.brellwick.com
          <svg class="icon" viewBox="0 0 12 12" aria-hidden="true"><circle cx="6" cy="6" r="5.5"/><path d="M6 0.5v11M0.5 6h11M6 0.5c-2.5 2.8-2.5 8.2 0 11M6 0.5c2.5 2.8 2.5 8.2 0 11" fill="none" stroke="#f6f6f6" stroke-width="0.8"/></svg>
        </li>
      </ul>
    </div>
  </section>

</main>
</body>
</html>
```